4th Generation Family Business Needs a New Card Design!

We are a family owned 4th Generation company. We are based in the Sydney, Australia area and we are desperately in need of a more modern and classy card. We are monumental masons who design, supply & erect lasting memorials throughout cemeteries in Sydney. Our customers are normally in a period of grieving. I have attached logo files that will need to be implemented on the card. Company was established 1935. Australian Owned and Operated. Card needs to be designed to PIXO.com specification.

Target Market(s)

Our target market is based upon people that a grieving for family members that have passed away. We also deal with alot of companies that own and operate cemeteries.

Industry/Entity Type

Business

Contact Information for Business Card

Simon Harcourt, Operations Manager, 0417293086, simon@harcourtmemorials.com.au
Lewis Harcourt, Director, 0491630572, lewis@harcourtmemorials.com.au
Phone # 02 9561 3048
Website: www.harcourtmemorials.com.au
Address: Suite 17, 8 Palfrey Lane, West Carlow, Sydney NSW 2156

Font styles to use
Serif
Decorative
Script

Requirements
Must have
• Would like to see the logo nicely implemented with a modern design. Embossed lettering would be a nice additive.

```html
<!DOCTYPE html>
<html lang="en">
<head>
<meta charset="utf-8">
<title>Harcourt Memorials – Business Card</title>
<link href="https://fonts.googleapis.com/css2?family=Cinzel:wght@500&family=Didact+Gothic&display=swap" rel="stylesheet">
<style>
  :root {
    --stage: #e9e7e3;
    --paper: #ffffff;
    --ink: #1d1d1d;
    --charcoal: #3a3a3c;
    --gold: #f0bb1f;
    --gold-soft: #f3c63f;
    --on-dark: #ffffff;
  }
  * { box-sizing: border-box; margin: 0; padding: 0; }
  html, body { width: 1200px; height: 892px; overflow: hidden; background: var(--stage); }
  .canvas {
    width: 1200px; height: 892px; position: relative;
    display: flex; align-items: center; justify-content: center; gap: 40px;
  }
  .card {
    width: 540px; height: 330px; position: relative; overflow: hidden;
    background: var(--paper);
    box-shadow: 0 6px 18px rgba(0,0,0,.18);
    font-family: "Didact Gothic", "Century Gothic", sans-serif;
  }
  .card-art { position: absolute; inset: 0; }

  /* logo wordmark */
  .wordmark {
    font-family: "Cinzel", serif; font-weight: 500; color: var(--ink);
    display: flex; align-items: center; gap: 10px; line-height: 1.05;
  }
  .wordmark-mark { width: 12px; height: 12px; background: var(--gold); flex: none; }

  /* contact side */
  .back .wordmark { position: absolute; left: 30px; top: 30px; font-size: 25px; letter-spacing: 1px; }
  .staff { position: absolute; left: 30px; top: 112px; display: flex; align-items: flex-start; }
  .person { padding-right: 12px; }
  .person + .person { padding-left: 12px; border-left: 2px solid var(--ink); }
  .person-name { font-size: 19px; color: var(--ink); line-height: 1.1; }
  .person-role { font-size: 13px; color: var(--gold); }

  .contacts {
    position: absolute; right: 18px; top: 206px;
    color: var(--on-dark); font-family: Arial, Helvetica, sans-serif;
    font-size: 12px; line-height: 14px; text-align: right;
  }
  .contact-row { display: flex; justify-content: flex-end; align-items: center; gap: 10px; margin-bottom: 3px; }
  .contact-row svg { width: 15px; height: 15px; flex: none; }

  /* logo side */
  .front { display: flex; align-items: center; justify-content: center; }
  .front .wordmark { font-size: 40px; letter-spacing: 2px; gap: 16px; }
  .front .wordmark-mark { width: 18px; height: 18px; }
</style>
</head>
<body>
<main class="canvas">

  <section class="card back" aria-label="Business card, contact side">
    <svg class="card-art" viewBox="0 0 540 330" aria-hidden="true">
      <path d="M0 205 Q320 198 540 95 L540 142 Q320 210 0 213 Z" fill="var(--gold-soft)"/>
      <path d="M0 216 Q320 213 540 145 L540 330 L0 330 Z" fill="var(--charcoal)"/>
    </svg>

    <div class="wordmark">
      <span class="wordmark-mark"></span>
      <span>Harcourt<br>Memorials</span>
    </div>

    <div class="staff">
      <div class="person">
        <div class="person-name">Simon Harcourt</div>
        <div class="person-role">Operations Manager</div>
      </div>
      <div class="person">
        <div class="person-name">Lewis Harcourt</div>
        <div class="person-role">Director</div>
      </div>
    </div>

    <div class="contacts">
      <div class="contact-row"><span>0417293086 / 0491630572</span>
        <svg viewBox="0 0 16 16"><rect width="16" height="16" rx="3" fill="var(--gold)"/><rect x="5" y="3" width="6" height="10" rx="1" fill="none" stroke="var(--charcoal)" stroke-width="1.4"/></svg></div>
      <div class="contact-row"><span>02 9561 3048</span>
        <svg viewBox="0 0 16 16"><rect width="16" height="16" rx="3" fill="var(--gold)"/><path d="M5 4 L7 4 L7.5 6.5 L6.5 7.3 Q7.5 9 8.8 9.6 L9.6 8.6 L12 9.2 L12 11 Q8 12 5 7 Z" fill="var(--charcoal)"/></svg></div>
      <div class="contact-row"><span>simon@harcourtmemorials.com.au<br>lewis@harcourtmemorials.com.au</span>
        <svg viewBox="0 0 16 16"><rect width="16" height="16" rx="3" fill="var(--gold)"/><rect x="3.5" y="5" width="9" height="6" fill="none" stroke="var(--charcoal)" stroke-width="1.2"/><path d="M3.5 5 L8 8.5 L12.5 5" fill="none" stroke="var(--charcoal)" stroke-width="1.2"/></svg></div>
      <div class="contact-row"><span>www.harcourtmemorials.com.au</span>
        <svg viewBox="0 0 16 16"><rect width="16" height="16" rx="3" fill="var(--gold)"/><circle cx="8" cy="8" r="4.5" fill="none" stroke="var(--charcoal)" stroke-width="1.2"/><path d="M3.5 8 H12.5 M8 3.5 V12.5" stroke="var(--charcoal)" stroke-width="1"/></svg></div>
      <div class="contact-row"><span>Suite 17, 8 Palfrey Lane, West Carlow,<br>Sydney NSW 2156</span>
        <svg viewBox="0 0 16 16"><rect width="16" height="16" rx="3" fill="var(--gold)"/><path d="M8 13 Q4 8.5 4 6.5 A4 4 0 0 1 12 6.5 Q12 8.5 8 13 Z" fill="var(--charcoal)"/><circle cx="8" cy="6.5" r="1.5" fill="var(--gold)"/></svg></div>
    </div>
  </section>

  <section class="card front" aria-label="Business card, logo side">
    <div class="wordmark">
      <span class="wordmark-mark"></span>
      <span>Harcourt<br>Memorials</span>
    </div>
  </section>

</main>
</body>
</html>
```